Ward Compass Business Card Design*

We need a business card design for our company Ward Compass. Our company is specialized in providing online consulting services regarding medical institutions, hospitals and doctors. We work with patients worldwide looking to choose between healthcare providers. We have a website you may use as a reference, where we list doctors and clinics worldwide. So we target Medical providers as well as patients worldwide.
Target Market(s)
Medical Providers and patients around the world
Industry/Entity Type
Medical
Contact Information for Business Card
Salwa Kettani
CEO
+90 612 348 2175
info@wardcompass.example
www.wardcompass.example
14 Annakhil 7 H.R.B. Rabat, Morocco
Requirements
Must have
- Company logo/name on one full side, personal info and smaller logo and company name on the other side.
Nice to have
- Smart and elegant design

```html
<!DOCTYPE html>
<html lang="en">
<head>
<meta charset="utf-8">
<title>Ward Compass – Business Card</title>
<link rel="stylesheet" href="https://fonts.googleapis.com/css2?family=Nunito+Sans:wght@300;400;800&display=swap">
<style>
  :root {
    --navy: #1a4475;
    --grey: #7f7c7d;
    --text: #3e3e42;
    --paper: #f3f3f5;
    --white: #ffffff;
    --stage: #e6e3de;
  }
  * { margin: 0; padding: 0; box-sizing: border-box; }
  html, body { width: 900px; height: 1200px; overflow: hidden; }
  body {
    background: var(--stage);
    font-family: "Nunito Sans", Arial, sans-serif;
    position: relative;
  }
  .card {
    position: absolute;
    left: 75px;
    width: 750px;
    height: 436px;
    box-shadow: 0 4px 10px rgba(0,0,0,0.25);
  }
  .card--front { top: 130px; background: var(--paper); }
  .card--back { top: 640px; background: var(--navy); }

  /* front */
  .brand-mark {
    position: absolute;
    left: 70px;
    top: 188px;
    display: flex;
    align-items: center;
    gap: 14px;
  }
  .brand-mark__dot {
    width: 46px; height: 46px; border-radius: 50%;
    background: var(--grey);
  }
  .brand-mark__name {
    font-weight: 800;
    font-size: 36px;
    color: var(--navy);
    letter-spacing: 0.5px;
  }
  .details {
    position: absolute;
    left: 437px;
    top: 124px;
    color: var(--text);
  }
  .details__name {
    font-size: 25px;
    font-weight: 300;
    color: var(--text);
    letter-spacing: 0.3px;
    line-height: 1.1;
  }
  .details__name strong { font-weight: 800; color: var(--navy); }
  .details__role {
    font-size: 18px;
    font-weight: 300;
    line-height: 1.2;
    margin-top: 2px;
  }
  .details__rule {
    width: 32px;
    height: 1px;
    background: var(--text);
    margin-top: 5px;
  }
  .details__address {
    font-size: 17.5px;
    font-weight: 400;
    line-height: 1.35;
    margin-top: 20px;
  }
  .contact { list-style: none; margin-top: 14px; }
  .contact__item {
    display: flex;
    align-items: center;
    gap: 18px;
    font-size: 17.5px;
    font-weight: 400;
    line-height: 26px;
  }
  .contact__icon { width: 20px; height: 20px; margin-left: -3px; }

  /* back */
  .back-brand {
    position: absolute;
    left: 0; right: 0;
    top: 186px;
    display: flex;
    justify-content: center;
    align-items: center;
    gap: 18px;
  }
  .back-brand__dot {
    width: 60px; height: 60px; border-radius: 50%;
    background: var(--grey);
  }
  .back-brand__name {
    font-weight: 800;
    font-size: 46px;
    color: var(--white);
    letter-spacing: 0.5px;
  }
  .back-url {
    position: absolute;
    left: 0; right: 0;
    top: 398px;
    text-align: center;
    color: var(--white);
    font-size: 16px;
    font-weight: 400;
    letter-spacing: 3.4px;
  }
</style>
</head>
<body>
  <section class="card card--front">
    <div class="brand-mark">
      <span class="brand-mark__dot"></span>
      <span class="brand-mark__name">Ward Compass</span>
    </div>
    <div class="details">
      <h1 class="details__name"><strong>SALWA</strong> KETTANI</h1>
      <p class="details__role">CEO</p>
      <div class="details__rule"></div>
      <p class="details__address">14 Annakhil 7 H.R.B.<br>Rabat, Morocco</p>
      <ul class="contact">
        <li class="contact__item">
          <svg class="contact__icon" viewBox="0 0 20 20" aria-hidden="true">
            <circle cx="10" cy="10" r="10" fill="var(--navy)"/>
            <path d="M7 5.2c.4-.3.9-.2 1.1.2l.9 1.6c.2.4.1.8-.2 1.1l-.6.5c.5 1.1 1.3 1.9 2.4 2.4l.5-.6c.3-.3.7-.4 1.1-.2l1.6.9c.4.2.5.7.2 1.1l-.6.8c-.4.5-1.1.7-1.7.4-2.5-1-4.4-2.9-5.4-5.4-.2-.6 0-1.3.4-1.7z" fill="var(--white)"/>
          </svg>
          <span>+90 612 348 2175</span>
        </li>
        <li class="contact__item">
          <svg class="contact__icon" viewBox="0 0 20 20" aria-hidden="true">
            <circle cx="10" cy="10" r="10" fill="var(--navy)"/>
            <rect x="5.5" y="7" width="9" height="6.4" rx="0.8" fill="var(--white)"/>
            <path d="M5.8 7.4L10 10.6l4.2-3.2" fill="none" stroke="var(--navy)" stroke-width="0.9"/>
          </svg>
          <span>info@wardcompass.example</span>
        </li>
      </ul>
    </div>
  </section>

  <section class="card card--back">
    <div class="back-brand">
      <span class="back-brand__dot"></span>
      <span class="back-brand__name">Ward Compass</span>
    </div>
    <p class="back-url">www.wardcompass.example</p>
  </section>
</body>
</html>
```